Gestaltung von Honigetiketten
Zielgruppe
Ich bin ein Imker, der im eigenen Restaurant seinen Honig ausstellen und verkaufen möchte.
Aufgabenstellung
Ich möchte exklusive und edle Honigetiketten die auffallen. Bevorzugt mit den Farben Gold und Schwarz, siehe meinem bisher gesehenen Favoriten im Anhang.
Nur das Logo selbst (Baum) soll übernommen werden Farbe kann variieren, ebenso die Schrift ist variabel.
Auf die Vorderseite des Honigetiketts soll zu lesen sein:
- Deutscher Honig
- Sommertracht
- 500g
- Logo und Name
Auf der Rückseite des Honigetiketts soll zu finden sein:
- freies Feld für Stempel für Namen und Adresse des Abfüllers
- freies Feld für das Mindesthaltbarkeitsdatum

```html
<!DOCTYPE html>
<html lang="de">
<head>
<meta charset="utf-8">
<title>Honigetikett Sommertracht</title>
<link rel="stylesheet" href="https://fonts.googleapis.com/css2?family=Kaushan+Script&family=Montserrat:wght@400;500&display=swap">
<style>
  :root {
    --gold: #f2a81d;
    --gold-deep: #b87a0c;
    --gold-glow: rgba(242, 168, 29, 0.55);
    --label-black: #0b0b0b;
    --pattern-base: #1a1204;
    --paper: #ffffff;
    --page: #f4f1ea;
    --ink: #111111;
  }
  * { box-sizing: border-box; margin: 0; padding: 0; }
  html, body {
    width: 1200px;
    height: 848px;
    overflow: hidden;
    background: var(--page);
  }
  .canvas {
    width: 1200px;
    height: 848px;
    display: flex;
    align-items: center;
    justify-content: center;
  }
  .label {
    width: 1100px;
    height: 345px;
    background: var(--label-black);
    display: flex;
    font-family: "Montserrat", sans-serif;
  }
  .honeycomb-pattern {
    height: 100%;
    background:
      radial-gradient(ellipse at 30% 25%, var(--gold-glow), transparent 55%),
      radial-gradient(ellipse at 75% 80%, var(--gold-glow), transparent 55%),
      linear-gradient(135deg, var(--gold-deep) 0%, var(--pattern-base) 45%, var(--pattern-base) 60%, var(--gold-deep) 100%);
  }
  .honeycomb-pattern--left { width: 262px; }
  .honeycomb-pattern--middle { width: 425px; }
  .honeycomb-pattern--right { width: 51px; }

  .front-panel, .back-panel {
    position: relative;
    height: 100%;
    flex-shrink: 0;
  }
  .front-panel { width: 176px; }
  .back-panel { width: 186px; }

  .brand {
    position: absolute;
    top: 24px;
    left: 0;
    width: 100%;
    display: flex;
    align-items: center;
    justify-content: center;
    gap: 6px;
    color: var(--gold);
    font-size: 11px;
    font-weight: 500;
    letter-spacing: 0.04em;
  }
  .brand-dot {
    width: 12px;
    height: 12px;
    border: 1.5px solid var(--gold);
    border-radius: 50%;
  }
  .harvest-tag {
    position: absolute;
    top: 70px;
    left: 50%;
    transform: translateX(-50%);
    background: var(--gold);
    color: var(--ink);
    font-size: 9px;
    font-weight: 500;
    letter-spacing: 0.05em;
    padding: 2px 6px;
    white-space: nowrap;
    font-variant: small-caps;
  }
  .title-disc {
    position: absolute;
    top: 121px;
    left: 13px;
    width: 150px;
    height: 150px;
    border-radius: 50%;
    background: var(--gold);
    display: flex;
    flex-direction: column;
    align-items: center;
    justify-content: center;
    font-family: "Kaushan Script", cursive;
    color: var(--ink);
    font-size: 28px;
    line-height: 1.15;
    text-align: center;
  }
  .weight-badge {
    position: absolute;
    top: 298px;
    left: 50%;
    transform: translateX(-50%);
    width: 34px;
    height: 32px;
  }
  .weight-badge text {
    font-family: "Montserrat", sans-serif;
    font-size: 8px;
    fill: var(--gold);
  }
  .stamp-field {
    position: absolute;
    top: 95px;
    left: 18px;
    width: 150px;
    height: 150px;
    border-radius: 50%;
    background: var(--paper);
    display: flex;
    flex-direction: column;
    align-items: center;
    justify-content: center;
    text-align: center;
    color: var(--ink);
    font-size: 10.5px;
    line-height: 1.65;
    white-space: nowrap;
  }
  .best-before-field {
    position: absolute;
    top: 264px;
    left: 41px;
    width: 104px;
    height: 23px;
    background: var(--paper);
    color: var(--ink);
    font-size: 11px;
    display: flex;
    align-items: center;
    justify-content: center;
  }
</style>
</head>
<body>
<main class="canvas">
  <section class="label">
    <div class="honeycomb-pattern honeycomb-pattern--left" role="img" aria-label="Goldenes Wabenmuster mit Bienen auf Schwarz"></div>

    <div class="front-panel">
      <div class="brand"><span class="brand-dot"></span><span>Lindenhof</span></div>
      <div class="harvest-tag">- Sommertracht -</div>
      <div class="title-disc"><span>Deutscher</span><span>Honig</span></div>
      <svg class="weight-badge" viewBox="0 0 34 32" aria-label="500 g">
        <polygon points="9,1.5 25,1.5 32.5,16 25,30.5 9,30.5 1.5,16" fill="none" stroke="var(--gold)" stroke-width="1"/>
        <text x="17" y="19" text-anchor="middle">500 G</text>
      </svg>
    </div>

    <div class="honeycomb-pattern honeycomb-pattern--middle" role="img" aria-label="Goldenes Wabenmuster mit Bienen auf Schwarz"></div>

    <div class="back-panel">
      <div class="stamp-field">
        <span>freies Feld für Stempel</span>
        <span>für Namen und Adresse</span>
        <span>des Abfüllers</span>
      </div>
      <div class="best-before-field">MhD</div>
    </div>

    <div class="honeycomb-pattern honeycomb-pattern--right" role="img" aria-label="Goldenes Wabenmuster auf Schwarz"></div>
  </section>
</main>
</body>
</html>
```